Letterhead Design for Law Firm

**Edit: I have added the photo of a bottom that I like.

------
We are looking for a re-design of our new letterhead. The letterhead is for a law firm and will be used for digital and traditionally printed correspondence.

Here are some suggestions:

- Please use colours are #8ec900 and simple black.
- Please do not use any type of "waves" at the bottom of the page. This is not in style at all.
- Please stay modern yet conservative.
- Please use font Segoe UI Light or similar if you can
- Avoid clipart or illustrations.
- Utilize ample white space in the layout so the design looks clean and information is easy to read at a glance. Don't overcrowd the letterhead.
- Make sure the letterhead design is consistent with our brand identity (see corvelith.ca)
-Please, no black headers or footers.

I am attaching my current letterhead and signature for your convenience.

Remember, the letterhead is an extension of our professional identity. We are a successful firm and trial lawyers who correspond with insurers, judges, lawyers, courts, clients, etc. Make it new, modern, attractive, yet powerful and conservative.

It needs to be easily printable. I would like the bleed removed in print so the black bar the bottom crosses the page (but the text is not near the edges)
Updates

Low design quality

Target Market(s)

Clients, Government Offices, Judiciary, Lawyers, Insurance Companies, Colleagues.

Industry/Entity Type

Law

Other font styles liked:
• Segoe UI LIght, Calibri Light,

Colors
00AB8E
00BBA5
67D7C9
C6EFE9
E9F9F6

Requirements
Must have
• Everything that is on the letterhead now.
Nice to have
• Cutting Edge design, yet conservative.
Should not have
• law firm cliche design, images,

```html
<!DOCTYPE html>
<html lang="en">
<head>
<meta charset="utf-8">
<title>Holloway Personal Injury Lawyers — Letterhead</title>
<link href="https://fonts.googleapis.com/css2?family=Lato:wght@400;700&family=Sora:wght@600&family=Open+Sans:wght@600&family=Didact+Gothic&family=Montserrat:wght@400;600&display=swap" rel="stylesheet">
<style>
  :root {
    --brand-green: #8ec900;
    --ink: #1a1a1a;
    --body-grey: #6e6e6e;
    --backdrop: #ebebee;
    --paper: #ffffff;
  }
  * { margin: 0; padding: 0; box-sizing: border-box; }
  html, body { width: 1068px; height: 1200px; overflow: hidden; background: var(--backdrop); }
  .letterhead {
    position: absolute; left: 121px; top: 20px;
    width: 1201px; height: 1685px;
    transform: scale(0.6884); transform-origin: 0 0;
    background: var(--paper);
    color: var(--ink);
    font-family: "Lato", sans-serif;
    overflow: hidden;
  }
  .firm-mark { position: absolute; left: 66px; top: 92px; width: 312px; text-align: center; }
  .firm-name { font-weight: 700; font-size: 58px; letter-spacing: 1px; line-height: 1; color: var(--ink); }
  .firm-tagline { margin-top: 12px; font-size: 17px; letter-spacing: 1.6px; text-transform: uppercase; color: var(--ink); }

  .firm-contact { position: absolute; left: 863px; top: 67px; font-size: 19px; line-height: 22px; }
  .firm-contact p { white-space: nowrap; }
  .firm-contact .gap { margin-top: 4px; }
  .firm-contact .label, .accent { color: var(--brand-green); }

  .recipient { position: absolute; left: 66px; top: 380px; font-family: "Montserrat", sans-serif; }
  .recipient-name { font-family: "Sora", sans-serif; font-weight: 600; font-size: 37px; line-height: 46px; }
  .recipient-line { font-size: 21px; margin-top: 12px; line-height: 26px; }
  .recipient-line.first { margin-top: 6px; }
  .recipient-line.tight { line-height: 28px; }

  .letter-date { position: absolute; right: 78px; top: 554px; font-family: "Open Sans", sans-serif; font-weight: 600; font-size: 25px; line-height: 34px; }

  .letter-body { position: absolute; left: 66px; top: 622px; width: 1057px; font-family: "Didact Gothic", sans-serif; font-size: 28px; letter-spacing: 0.4px; line-height: 37.3px; color: var(--body-grey); text-align: justify; hyphens: auto; }
  .letter-body p + p { margin-top: 37.3px; }

  .signatory { position: absolute; right: 85px; top: 1263px; font-family: "Montserrat", sans-serif; font-weight: 600; font-size: 29px; line-height: 38px; }
  .signature-area { position: absolute; left: 868px; top: 1324px; width: 185px; height: 116px; background: linear-gradient(135deg, #f3f3f3, #e6e6e6); border-radius: 4px; }

  .practice-areas { position: absolute; left: 52px; right: 0; top: 1574px; font-size: 19.5px; line-height: 28px; white-space: nowrap; }
  .practice-areas .title { color: var(--brand-green); font-weight: 700; }
  .practice-areas .second-line { display: flex; align-items: center; }
  .practice-areas .rule { flex: 1; height: 1.5px; background: var(--ink); margin-left: 6px; margin-top: 3px; }
</style>
</head>
<body>
<main class="letterhead">
  <header>
    <div class="firm-mark">
      <div class="firm-name">HOLLOWAY</div>
      <div class="firm-tagline">Personal Injury Lawyers</div>
    </div>
    <div class="firm-contact">
      <p>www.<span class="accent">CORVELITH</span>.ca</p>
      <p class="gap">48 Harbour Road E, Suite 902</p>
      <p>Hamilton, ON&nbsp; L8N 3B2</p>
      <p class="gap"><span class="label">T:</span> 905-410-2266</p>
      <p class="gap"><span class="label">F:</span> 905-410-2270</p>
      <p class="gap"><span class="label">File Clerk:</span> Maren Ashdown</p>
      <p class="gap"><span class="label">Email:</span> maren@corvelith.ca</p>
    </div>
  </header>

  <section class="recipient">
    <h1 class="recipient-name">Jone Smith</h1>
    <p class="recipient-line first">0123-456-789</p>
    <p class="recipient-line">info@youremailaddress.com</p>
    <p class="recipient-line tight">1234 City Your Ln. Suite<br>123 Dallas, TX 0000</p>
  </section>

  <p class="letter-date">12 December, 2024</p>

  <article class="letter-body" lang="en">
    <p>Lorem ipsum dolor sit amet, consectetuer adipiscing elit, sed diam nonummy nibh euismod tincidunt ut laoreet dolore magna aliquam erat volutpat. Ut wisi enim ad minim veniam, quis nostrud exerci tation ullamcorper suscipit lobortis nisl ut aliquip ex ea commodo consequat. Duis autem vel eum iriure dolor in hendrerit in vulputate velit esse molestie consequat, vel illum dolore eu feugiat nulla facilisis at vero eros et accumsan et iusto odio dignissim qui blandit praesent luptatum zzril delenit augue duis dolore te feugait nulla facilisi.</p>
    <p>Lorem ipsum dolor sit amet, cons ectetuer adipiscing elit, sed diam nonummy nibh euismod tincidunt ut laoreet dolore magna aliquam erat volutpat. Ut wisi enim ad minim veniam, quis nostrud exerci tation ullamcorper suscipit lobortis nisl ut aliquip ex ea commodo consequat.</p>
    <p>Lorem ipsum dolor sit amet, consectetuer adipiscing elit, sed diam nonummy nibh euismod tincidunt ut laoreet dolore magna aliquam erat</p>
  </article>

  <p class="signatory">Mr. Daniel P. Whitcombe</p>
  <div class="signature-area" role="img" aria-label="Handwritten signature of the signatory"></div>

  <footer class="practice-areas">
    <div><span class="title">Practice Restricted //</span> Serious Personal Injury <span class="accent">•</span> Wrongful Death Litigation <span class="accent">•</span> Long-Term Disability Litigation</div>
    <div class="second-line"><span><span class="accent">•</span> Wrongful Dismissal Litigation <span class="accent">•</span> Employee Terminations</span><span class="rule"></span></div>
  </footer>
</main>
</body>
</html>
```